Residential Remodeling Contractor needs updated business card

I need a new design for my business card.
Name of the company is Ridgefell Construction. I need a card that commands presence, strength, integrity. I have been in business for 28 years. I am a Residential Remodeling Contractor that covers all aspects of a residential remodel and build.

```html
<!DOCTYPE html>
<html lang="en">
<head>
<meta charset="utf-8">
<title>Ridgefell Construction — Business Card</title>
<link rel="stylesheet" href="https://fonts.googleapis.com/css2?family=Libre+Baskerville:wght@700&family=Arimo:wght@400&display=swap">
<style>
  :root {
    --navy: #183c7a;
    --ink: #3a3a3a;
    --paper: #ffffff;
    --backdrop: #9a9a9a;
    --serif: "Libre Baskerville", Georgia, serif;
    --sans: "Arimo", Arial, sans-serif;
  }
  * { margin: 0; padding: 0; box-sizing: border-box; }
  html, body { width: 1200px; height: 1059px; overflow: hidden; }
  body { background: var(--backdrop); position: relative; font-family: var(--sans); }

  .card {
    position: absolute;
    left: 256px;
    width: 688px;
    height: 391px;
    border-radius: 24px;
    overflow: hidden;
  }
  .card--front { top: 89px; background: var(--paper); }
  .card--back  { top: 569px; background: var(--navy); }

  .brand-name {
    position: absolute;
    left: 0; right: 0;
    display: flex;
    align-items: center;
    justify-content: center;
    font-family: var(--serif);
    font-weight: 700;
    line-height: 1;
    white-space: nowrap;
  }
  .brand-name__mark { flex: none; }

  .card--front .brand-name { top: 96px; color: var(--navy); font-size: 26px; gap: 14px; }
  .card--front .brand-name__mark { width: 20px; height: 20px; background: var(--navy); }

  .card--back .brand-name { top: 176px; color: var(--paper); font-size: 40px; gap: 20px; }
  .card--back .brand-name__mark { width: 30px; height: 30px; background: var(--paper); }

  .person { position: absolute; left: 0; right: 0; top: 209px; text-align: center; }
  .person__name { font-family: var(--serif); font-weight: 700; font-size: 19.5px; color: var(--navy); letter-spacing: 0.3px; line-height: 24px; }
  .person__role { font-size: 16px; color: var(--ink); margin-top: 2px; }

  .address {
    position: absolute; right: 364px; top: 294px;
    text-align: right; font-size: 16px; line-height: 21px; color: var(--ink);
  }
  .divider { position: absolute; left: 344px; top: 291px; width: 1px; height: 54px; background: var(--navy); }

  .contacts { position: absolute; left: 366px; top: 282px; list-style: none; font-size: 16px; color: var(--ink); }
  .contacts li { display: flex; align-items: center; height: 22.5px; }
  .contacts svg { width: 12px; height: 12px; margin-right: 9px; fill: var(--navy); }
  .contacts .site-name { color: var(--navy); }

  .base-band { position: absolute; left: 0; right: 0; bottom: 0; height: 10px; background: var(--navy); }
</style>
</head>
<body>

  <section class="card card--front" aria-label="Card front">
    <div class="brand-name">
      <span class="brand-name__mark"></span>
      <span>Ridgefell Construction</span>
    </div>

    <div class="person">
      <p class="person__name">DANIEL OSTRANDER</p>
      <p class="person__role">Owner &amp; Manager</p>
    </div>

    <p class="address">P.O. Box&nbsp; Street Name<br>Country Name AB, A5B 521</p>
    <span class="divider"></span>

    <ul class="contacts">
      <li>
        <svg viewBox="0 0 12 12" aria-hidden="true"><path d="M1 4.5C1 2.5 3 2 6 2s5 .5 5 2.5v1H8.5V4.2h-5v1.3H1z"/><rect x="2" y="6" width="8" height="4.5" rx="1"/></svg>
        555 014 2387
      </li>
      <li>
        <svg viewBox="0 0 12 12" aria-hidden="true"><path d="M1 5l5-3.5L11 5v5.5H1z M2.3 5.4L6 8l3.7-2.6L6 2.9z"/></svg>
        info@ridgefellconstruction.com
      </li>
      <li>
        <svg viewBox="0 0 12 12" aria-hidden="true"><circle cx="6" cy="6" r="5.2"/><path d="M4 3.2c1 .3 1.6 1.2 1 2-.6.8-1.8.6-1.6 1.8.2 1 1.3 1 1.4 2.6M8 2.8c-.4 1 .4 1.6 1.3 1.8M8.8 7.5c-.8.2-1.4.9-1.2 2" stroke="#fff" stroke-width="1" fill="none"/></svg>
        <span>www.<span class="site-name">ridgefellconstruction</span>.com</span>
      </li>
    </ul>

    <span class="base-band"></span>
  </section>

  <section class="card card--back" aria-label="Card back">
    <div class="brand-name">
      <span class="brand-name__mark"></span>
      <span>Ridgefell Construction</span>
    </div>
  </section>

</body>
</html>
```